New Business Card Design Project

Need a design that will create an impact / strong impression towards our clients for our business. We are in the lighting business and we do lighting retrofits for large commercial to industrial clientele.

Target Market(s)

Lighting Industry

Industry/Entity Type

Business

Font styles to use
Other font styles liked:
• we would like to use the font on our logo, not sure what it is though..

Requirements
Must have
• Our logo.
Nice to have
• We are open to suggestions that have to do with lighting.

```html
<!DOCTYPE html>
<html lang="en">
<head>
<meta charset="utf-8">
<title>Lumenway Retrofit Group – Business Card</title>
<link href="https://fonts.googleapis.com/css2?family=Lato:wght@400;700&display=swap" rel="stylesheet">
<style>
  :root {
    --backdrop: #3b3b3d;
    --card: #ffffff;
    --green: #118a3c;
    --green-dark: #0f3d17;
    --ink: #1d1d1d;
  }
  * { box-sizing: border-box; margin: 0; padding: 0; }
  html, body { width: 1200px; height: 900px; overflow: hidden; }
  body {
    background: var(--backdrop);
    font-family: 'Lato', sans-serif;
    color: var(--ink);
    position: relative;
  }
  .card {
    position: absolute;
    left: 250px;
    width: 700px;
    height: 400px;
    background: var(--card);
    box-shadow: 0 6px 18px rgba(0,0,0,.35);
    overflow: hidden;
  }
  .card--front { top: 30px; }
  .card--back { top: 470px; }

  .wordmark {
    display: flex;
    align-items: center;
    gap: 14px;
    color: var(--green);
    font-weight: 700;
    white-space: nowrap;
  }
  .wordmark__square {
    width: 0.8em;
    height: 0.8em;
    background: var(--green);
    flex: none;
  }
  .card--front .wordmark {
    position: absolute;
    top: 140px;
    left: 0; right: 0;
    justify-content: center;
    font-size: 44px;
  }
  .card--front .website {
    position: absolute;
    top: 295px;
    left: 0; right: 0;
    text-align: center;
    font-size: 17px;
    letter-spacing: 1.5px;
  }

  .card--back .wordmark {
    position: absolute;
    top: 42px;
    left: 44px;
    font-size: 32px;
  }
  .person { position: absolute; top: 118px; left: 44px; }
  .person__name { color: var(--green); font-size: 30px; font-weight: 700; }
  .person__title { font-size: 19px; margin-top: 2px; }

  .contacts {
    position: absolute;
    top: 198px;
    left: 44px;
    list-style: none;
    font-size: 20px;
  }
  .contacts li { display: flex; align-items: center; gap: 12px; height: 28px; }
  .contacts svg { width: 18px; height: 18px; fill: var(--green); flex: none; }

  .address {
    position: absolute;
    right: 60px;
    top: 262px;
    text-align: right;
    font-size: 20px;
    line-height: 1.3;
  }
  .band { position: absolute; left: 0; top: 326px; width: 700px; height: 38px; }
  .band__url {
    position: absolute;
    left: 44px;
    top: 330px;
    color: #fff;
    font-size: 21px;
  }
</style>
</head>
<body>

<section class="card card--front">
  <div class="wordmark"><span class="wordmark__square"></span>Lumenway Retrofit Group</div>
  <p class="website">www.lumenway-retrofit.com</p>
</section>

<section class="card card--back">
  <div class="wordmark"><span class="wordmark__square"></span>Lumenway Retrofit Group</div>

  <div class="person">
    <p class="person__name">Evan Marsh</p>
    <p class="person__title">Manager</p>
  </div>

  <ul class="contacts">
    <li>
      <svg viewBox="0 0 24 24" aria-hidden="true"><path d="M6.6 10.8a15.1 15.1 0 0 0 6.6 6.6l2.2-2.2a1 1 0 0 1 1-.25 11.4 11.4 0 0 0 3.6.57 1 1 0 0 1 1 1V20a1 1 0 0 1-1 1A17 17 0 0 1 3 4a1 1 0 0 1 1-1h3.5a1 1 0 0 1 1 1c0 1.25.2 2.45.57 3.57a1 1 0 0 1-.25 1z"/></svg>
      (555) 214-3800
    </li>
    <li>
      <svg viewBox="0 0 24 24" aria-hidden="true"><path d="M7 3h10v5H7zM4 9h16a2 2 0 0 1 2 2v6h-4v4H6v-4H2v-6a2 2 0 0 1 2-2zm4 7v3h8v-3z"/></svg>
      (555) 214-3801
    </li>
    <li>
      <svg viewBox="0 0 24 24" aria-hidden="true"><path d="M2 5h20v14H2zm2 2v.5l8 5 8-5V7zm0 2.8V17h16V9.8l-8 5z"/></svg>
      hello@lumenway-retrofit.com
    </li>
  </ul>

  <p class="address">218 Alder Park Road<br>Fairview, IL 60500</p>

  <svg class="band" viewBox="0 0 700 38" aria-hidden="true">
    <polygon points="0,0 590,0 572,38 0,38" fill="var(--green)"/>
    <polygon points="602,0 650,0 632,38 584,38" fill="var(--green-dark)"/>
    <polygon points="662,0 700,0 700,38 644,38" fill="var(--green)"/>
  </svg>
  <p class="band__url">www.lumenway-retrofit.com</p>
</section>

</body>
</html>
```